QuillVane needs a dashboard page designed

Redesign the dashboard shown in the provided images.

There are two images:
- dashboard.png
- dashboard-expanded.png

NOTE: The vocabulary navigation on the left will be a very long list of words 100s, so keep that in mind when you're designing both the vocab navigation and the expanded vocab popup.

In the dashboard.png picture, there needs to be a progress chart showing the word progress like the following: review 1(show it as completed) -> review 2(show the user they are here) -> review 3(unvisited) -> review 4(unvisited)

The do-not-design-this-page.png image is for your reference only. It is not to be designed. Use it to understand the overall look and feel of the website to help you create the best dashboard page possible.
Updates

Need extra days to review

Industry/Entity Type

Education English learning

Number of Pages Required

1 page

Requirements
Must have
• The main navigation and main header cannot change between pages. See the do-not-design page for the main navigateion and header.
Should not have
• Do not add a person profile. We will not have images of our users. Keep the icons in the main navigation as they are.

```html
<!DOCTYPE html>
<html lang="en">
<head>
<meta charset="utf-8">
<title>QuillVane Dashboard</title>
<link rel="stylesheet" href="https://fonts.googleapis.com/css2?family=Inter:wght@400;500;600;700&display=swap">
<style>
:root{
  --stage:#ababab;
  --bar-dark:#262b33;
  --rail:#2a2f37;
  --rail-active:#3a4049;
  --page:#f7f8fa;
  --white:#ffffff;
  --line:#e7e9ee;
  --ink:#1d2129;
  --muted:#5a5f69;
  --faint:#a3a8b1;
  --blue:#2a5db0;
  --row-active:#eef2fa;
  --orange:#f6a52a;
  --purple:#5b4cf0;
  --red:#e8305a;
  --sky:#1e88e5;
  --chip-purple:#eeedfd;
  --chip-red:#fde9ee;
  --chip-orange:#fff4e3;
}
*{box-sizing:border-box;margin:0;padding:0}
html,body{width:933px;height:1200px;overflow:hidden;background:var(--stage);font-family:"Inter",sans-serif;color:var(--ink)}
.screen{position:absolute;left:30px;width:1440px;height:915px;background:var(--page);transform-origin:0 0;transform:scale(.60625);overflow:hidden}
.screen.first{top:30px}
.screen.second{top:614px}
.abs{position:absolute}
.topbar{left:0;top:0;width:1440px;height:35px;background:var(--bar-dark)}
.topbar .title{left:0;width:1440px;top:8px;text-align:center;color:#fff;font-size:15px;font-weight:500}
.rail{left:0;top:35px;width:78px;height:880px;background:var(--rail)}
.rail-item{left:0;width:78px;text-align:center;color:#e5e7eb;font-size:9px;white-space:nowrap}
.rail-item.active{background:var(--rail-active)}
.rail-item svg{display:block;margin:0 auto 4px}
.sidebar{left:78px;top:35px;width:283px;height:862px;background:var(--white);border-right:1px solid var(--line)}
.sb-filter{left:12px;top:24px;font-size:16px;font-weight:600;white-space:nowrap}
.sb-expand{right:16px;top:24px;font-size:16px;font-weight:500;color:var(--blue)}
.sb-row{left:0;width:283px;height:43px;border-bottom:1px solid var(--line);font-size:16px;font-weight:500;padding:12px 20px;white-space:nowrap}
.sb-row.word{background:var(--row-active);font-weight:400;border-bottom:none}
.sb-row svg{position:absolute;right:18px;top:15px}
.step{top:60px;width:250px;height:57px;white-space:nowrap}
.step svg.shape{position:absolute;left:0;top:0}
.step .name{position:absolute;left:16px;top:10px;font-size:15px;font-weight:500}
.step .state{position:absolute;left:16px;top:32px;font-size:12px}
.step .badge{position:absolute;top:9px;width:40px;height:40px;border-radius:50%;display:flex;align-items:center;justify-content:center}
.word-title{left:394px;top:160px;font-size:27px;font-weight:700;display:flex;align-items:center;gap:12px}
.start-btn{left:1083px;top:152px;width:342px;height:47px;border-radius:24px;background:var(--bar-dark);color:#fff;font-size:16px;font-weight:600;display:flex;align-items:center;justify-content:center;gap:12px;white-space:nowrap}
.intro{left:394px;top:236px;width:1020px;font-size:14px;line-height:24px;color:var(--muted)}
.card{left:394px;top:330px;width:1031px;height:388px;background:var(--white);border:1px solid var(--line);border-radius:16px}
.card-icon{left:24px;top:23px;width:48px;height:48px;border-radius:50%;background:#edf1f8;display:flex;align-items:center;justify-content:center}
.card-title{left:84px;top:36px;font-size:19px;font-weight:500;white-space:nowrap}
.tabs{right:25px;top:27px;height:41px;border-radius:21px;background:#f1f3f6;display:flex;align-items:center;padding:0 4px;font-size:14px;font-weight:500;color:#3b4049;white-space:nowrap}
.tabs span{flex:none;padding:0 11px;line-height:33px;white-space:nowrap}
.tabs .on{background:var(--white);border-radius:17px;color:var(--ink);padding:0 12px}
.legend{left:44px;font-size:14px;font-weight:500;white-space:nowrap}
.analysis-title{left:394px;top:756px;font-size:18px;font-weight:700;white-space:nowrap}
.analysis{left:394px;top:798px;width:1000px;font-size:14px;line-height:24px;color:var(--muted)}
.bottom-strip{top:897px;height:18px;background:var(--white)}
.dim{left:0;top:0;width:1440px;height:915px;background:rgba(20,22,26,.45)}
.modal{left:467px;top:253px;width:507px;height:409px;background:var(--white);border-radius:8px}
.modal-head{left:8px;top:7px;width:491px;height:48px;background:var(--blue);border-radius:4px;color:#fff;font-size:16px;font-weight:600;padding:13px 22px;display:flex;align-items:center;gap:10px}
.modal-close{right:12px;top:10px;width:28px;height:28px;border-radius:50%;background:#fde4e8;display:flex;align-items:center;justify-content:center}
.group-title{left:30px;font-size:15px;font-weight:500;white-space:nowrap}
.chips{left:30px;width:460px;display:flex;flex-wrap:wrap;gap:12px 11px}
.chip{height:30px;line-height:30px;padding:0 12px;border-radius:3px;font-size:13px;white-space:nowrap}
.chip.red{background:var(--chip-red);color:var(--red)}
.chip.purple{background:var(--chip-purple);color:var(--purple)}
.chip.orange{background:var(--chip-orange);color:var(--orange)}
</style>
</head>
<body>

<!-- Dashboard view -->
<section class="screen first">
  <header class="abs topbar">
    <div class="abs title">Daily English &#9662;</div>
    <svg class="abs" style="left:1304px;top:8px" width="20" height="20" viewBox="0 0 20 20"><circle cx="10" cy="10" r="6" fill="none" stroke="#fff" stroke-width="4" stroke-dasharray="3 2"/><circle cx="10" cy="10" r="2.5" fill="#fff"/></svg>
    <svg class="abs" style="left:1345px;top:7px" width="20" height="20" viewBox="0 0 20 20"><path d="M10 2l7 3v5c0 4-3 7-7 8-4-1-7-4-7-8V5z" fill="#fff"/><path d="M6.5 10l2.5 2.5 4.5-5" stroke="#262b33" stroke-width="2" fill="none"/></svg>
    <svg class="abs" style="left:1390px;top:6px" width="36" height="22" viewBox="0 0 36 22"><circle cx="11" cy="11" r="10" fill="#fff"/><circle cx="11" cy="8" r="3.5" fill="#262b33"/><path d="M4.5 17c2-3 11-3 13 0" stroke="#262b33" stroke-width="2.5" fill="none"/><path d="M28 9l3 3 3-3" stroke="#fff" stroke-width="1.6" fill="none"/></svg>
  </header>
  <nav class="abs rail">
    <div class="abs rail-item active" style="top:0;height:70px;padding-top:19px"><svg width="16" height="16" viewBox="0 0 16 16"><path d="M8 1l7 6h-2v8H9v-5H7v5H3V7H1z" fill="#fff"/></svg>QuillVane</div>
    <div class="abs rail-item" style="top:92px"><svg width="22" height="20" viewBox="0 0 22 20"><path d="M1 5l6-3 8 3 6-3v13l-6 3-8-3-6 3z" fill="#fff"/><circle cx="11" cy="7" r="3" fill="#2a2f37"/></svg>Daily English</div>
    <div class="abs rail-item" style="top:168px"><svg width="16" height="20" viewBox="0 0 16 20"><rect x="1" y="1" width="14" height="18" fill="#fff"/><g fill="#2a2f37"><rect x="4" y="4" width="3" height="3"/><rect x="9" y="4" width="3" height="3"/><rect x="4" y="9" width="3" height="3"/><rect x="9" y="9" width="3" height="3"/><rect x="6" y="14" width="4" height="5"/></g></svg>Business</div>
  </nav>
  <aside class="abs sidebar">
    <div class="abs sb-filter">All &nbsp;<svg width="14" height="9" viewBox="0 0 14 9"><path d="M1 1l6 6 6-6" stroke="#1d2129" stroke-width="1.8" fill="none"/></svg></div>
    <div class="abs sb-expand">Expand</div>
    <div class="abs sb-row" style="top:63px;border-bottom:none">Short-Term Memory<svg width="18" height="10" viewBox="0 0 18 10"><path d="M1 9l8-7 8 7" stroke="#555" stroke-width="1.6" fill="none"/></svg></div>
    <div class="abs sb-row word" style="top:106px;height:41px">Grab</div>
    <div class="abs sb-row" style="top:147px;border-top:1px solid var(--line)">Working Memory<svg width="18" height="10" viewBox="0 0 18 10"><path d="M1 1l8 7 8-7" stroke="#555" stroke-width="1.6" fill="none"/></svg></div>
    <div class="abs sb-row" style="top:191px">Long-Term Memory<svg width="18" height="10" viewBox="0 0 18 10"><path d="M1 1l8 7 8-7" stroke="#555" stroke-width="1.6" fill="none"/></svg></div>
  </aside>

  <div class="abs step" style="left:394px">
    <svg class="shape" width="250" height="57"><polygon points="0,0 235,0 247,28.5 235,57 0,57" fill="#2a5db0"/></svg>
    <div class="name" style="color:#fff">Review 1</div><div class="state" style="color:#dfe7f5">Completed</div>
    <div class="badge" style="left:188px;background:#fff"><svg width="18" height="18" viewBox="0 0 24 24"><path d="M12 2l3 7 7 .6-5.3 4.7 1.6 7.2L12 17.8 5.7 21.5l1.6-7.2L2 9.6 9 9z" fill="#f6a52a"/></svg></div>
  </div>
  <div class="abs step" style="left:652px">
    <svg class="shape" width="250" height="57"><polygon points="1,1 235,1 247,28.5 235,56 1,56 12,28.5" fill="#fff" stroke="#2a5db0" stroke-width="1.5"/></svg>
    <div class="name" style="left:34px">Review 2</div><div class="state" style="left:34px;color:var(--muted)">In Process</div>
    <div class="badge" style="left:192px;background:#2a5db0"><svg width="18" height="18" viewBox="0 0 24 24"><path d="M12 2l3 7 7 .6-5.3 4.7 1.6 7.2L12 17.8 5.7 21.5l1.6-7.2L2 9.6 9 9z" fill="#fff"/></svg></div>
  </div>
  <div class="abs step" style="left:909px">
    <svg class="shape" width="250" height="57"><polygon points="1,1 235,1 247,28.5 235,56 1,56 12,28.5" fill="#fafbfc" stroke="#eceef2"/></svg>
    <div class="name" style="left:29px;color:var(--faint)">Review 3</div><div class="state" style="left:29px;color:var(--faint)">Unvisited</div>
    <div class="badge" style="left:195px;background:#eef0f3"><svg width="18" height="18" viewBox="0 0 24 24"><path d="M12 2l3 7 7 .6-5.3 4.7 1.6 7.2L12 17.8 5.7 21.5l1.6-7.2L2 9.6 9 9z" fill="none" stroke="#9aa0a9" stroke-width="1.6"/></svg></div>
  </div>
  <div class="abs step" style="left:1167px">
    <svg class="shape" width="250" height="57"><polygon points="1,1 235,1 247,28.5 235,56 1,56 12,28.5" fill="#fafbfc" stroke="#eceef2"/></svg>
    <div class="name" style="left:29px;color:var(--faint)">Review 4</div><div class="state" style="left:29px;color:var(--faint)">Unvisited</div>
    <div class="badge" style="left:195px;background:#eef0f3"><svg width="18" height="18" viewBox="0 0 24 24"><path d="M12 2l3 7 7 .6-5.3 4.7 1.6 7.2L12 17.8 5.7 21.5l1.6-7.2L2 9.6 9 9z" fill="none" stroke="#9aa0a9" stroke-width="1.6"/></svg></div>
  </div>

  <h1 class="abs word-title">Grab <svg width="24" height="24" viewBox="0 0 24 24"><path d="M12 2l3 7 7 .6-5.3 4.7 1.6 7.2L12 17.8 5.7 21.5l1.6-7.2L2 9.6 9 9z" fill="#f2b705"/></svg></h1>
  <div class="abs start-btn"><svg width="20" height="20" viewBox="0 0 20 20"><circle cx="10" cy="10" r="10" fill="#fff"/><path d="M8 6l6 4-6 4z" fill="#262b33"/></svg>Start Vocabulary Review Exercise 3</div>
  <p class="abs intro">The word "grab" is most commonly used as a verb, meaning to take something quickly or suddenly. Imagine you're running late for school. You don't have time for breakfast, so you quickly grab an apple from the kitchen and rush out the door. As you reach the bus stop, your friend waves and says, "Hey! Let's grab a coffee after class." Later, when you sit down, your phone starts ringing. You grab it from your bag and answer.</p>

  <div class="abs card">
    <div class="abs card-icon"><svg width="22" height="20" viewBox="0 0 22 20"><path d="M2 18h18M3 18V9l4 3V6l4 3V3l4 3v12" stroke="#2a5db0" stroke-width="1.8" fill="none"/><path d="M15 5l3-3 2 2" stroke="#2a5db0" stroke-width="1.6" fill="none"/></svg></div>
    <div class="abs card-title">Learning Curve Graph</div>
    <div class="abs tabs"><span>1 day</span><span>1 week</span><span>1 month</span><span>1 year</span><span class="on">All Time</span></div>
    <div class="abs legend" style="top:121px;color:var(--orange)">Long-Term Memory</div>
    <div class="abs legend" style="top:172px;color:var(--purple)">Working Memory</div>
    <div class="abs legend" style="top:223px;color:var(--red)">Short-Term Memory</div>
    <div class="abs legend" style="top:274px;color:var(--sky)">Forgotten Memory</div>
    <svg class="abs" style="left:0;top:0" width="1031" height="388" viewBox="394 330 1031 388">
      <g stroke="#eceef2"><line x1="676" x2="1401" y1="459" y2="459"/><line x1="676" x2="1401" y1="510" y2="510"/><line x1="676" x2="1401" y1="561" y2="561"/><line x1="676" x2="1401" y1="612" y2="612"/><line x1="676" x2="1401" y1="661" y2="661"/></g>
      <g>
        <path d="M678 661V524a16 16 0 0 1 32 0V661z" fill="#5b4cf0"/>
        <path d="M740 661V475a16 16 0 0 1 32 0V661z" fill="#f6a52a"/>
        <path d="M802 661V627a16 16 0 0 1 32 0V661z" fill="#1e88e5"/>
        <path d="M864 661V577a16 16 0 0 1 32 0V661z" fill="#e8305a"/>
        <path d="M926 661V475a16 16 0 0 1 32 0V661z" fill="#f6a52a"/>
        <path d="M988 661V524a16 16 0 0 1 32 0V661z" fill="#5b4cf0"/>
        <path d="M1050 661V627a16 16 0 0 1 32 0V661z" fill="#1e88e5"/>
        <path d="M1112 661V577a16 16 0 0 1 32 0V661z" fill="#e8305a"/>
        <path d="M1174 661V475a16 16 0 0 1 32 0V661z" fill="#f6a52a"/>
        <path d="M1236 661V627a16 16 0 0 1 32 0V661z" fill="#1e88e5"/>
        <path d="M1298 661V524a16 16 0 0 1 32 0V661z" fill="#5b4cf0"/>
        <path d="M1360 661V577a16 16 0 0 1 32 0V661z" fill="#e8305a"/>
      </g>
      <g font-family="Inter, sans-serif" font-size="12" fill="#444" text-anchor="middle">
        <text x="694" y="685">Jan</text><text x="756" y="685">Feb</text><text x="818" y="685">Mar</text><text x="880" y="685">Apr</text><text x="942" y="685">May</text><text x="1004" y="685">Jun</text><text x="1066" y="685">Jul</text><text x="1128" y="685">Aug</text><text x="1190" y="685">Sep</text><text x="1252" y="685">Oct</text><text x="1314" y="685">Nov</text><text x="1376" y="685">Dec</text>
      </g>
    </svg>
  </div>

  <h2 class="abs analysis-title">QuillVane Learning Analysis</h2>
  <p class="abs analysis">Lorem ipsum dolor sit amet, consectetur adipiscing elit, sed do eiusmod tempor incididunt ut labore et dolore magna aliqua. Ut enim ad minim veniam, quis nostrud exercitation ullamco laboris nisi ut aliquip ex ea commodo consequat.</p>
  <div class="abs bottom-strip" style="left:78px;width:1362px"></div>
</section>

<!-- Expanded vocabulary view -->
<section class="screen second">
  <header class="abs topbar">
    <div class="abs title">Daily English &#9662;</div>
    <svg class="abs" style="left:1304px;top:8px" width="20" height="20" viewBox="0 0 20 20"><circle cx="10" cy="10" r="6" fill="none" stroke="#fff" stroke-width="4" stroke-dasharray="3 2"/><circle cx="10" cy="10" r="2.5" fill="#fff"/></svg>
    <svg class="abs" style="left:1345px;top:7px" width="20" height="20" viewBox="0 0 20 20"><path d="M10 2l7 3v5c0 4-3 7-7 8-4-1-7-4-7-8V5z" fill="#fff"/><path d="M6.5 10l2.5 2.5 4.5-5" stroke="#262b33" stroke-width="2" fill="none"/></svg>
    <svg class="abs" style="left:1390px;top:6px" width="36" height="22" viewBox="0 0 36 22"><circle cx="11" cy="11" r="10" fill="#fff"/><circle cx="11" cy="8" r="3.5" fill="#262b33"/><path d="M4.5 17c2-3 11-3 13 0" stroke="#262b33" stroke-width="2.5" fill="none"/><path d="M28 9l3 3 3-3" stroke="#fff" stroke-width="1.6" fill="none"/></svg>
  </header>
  <nav class="abs rail">
    <div class="abs rail-item active" style="top:0;height:70px;padding-top:19px"><svg width="16" height="16" viewBox="0 0 16 16"><path d="M8 1l7 6h-2v8H9v-5H7v5H3V7H1z" fill="#fff"/></svg>QuillVane</div>
    <div class="abs rail-item" style="top:92px"><svg width="22" height="20" viewBox="0 0 22 20"><path d="M1 5l6-3 8 3 6-3v13l-6 3-8-3-6 3z" fill="#fff"/><circle cx="11" cy="7" r="3" fill="#2a2f37"/></svg>Daily English</div>
    <div class="abs rail-item" style="top:168px"><svg width="16" height="20" viewBox="0 0 16 20"><rect x="1" y="1" width="14" height="18" fill="#fff"/><g fill="#2a2f37"><rect x="4" y="4" width="3" height="3"/><rect x="9" y="4" width="3" height="3"/><rect x="4" y="9" width="3" height="3"/><rect x="9" y="9" width="3" height="3"/><rect x="6" y="14" width="4" height="5"/></g></svg>Business</div>
  </nav>
  <aside class="abs sidebar">
    <div class="abs sb-filter">All &nbsp;<svg width="14" height="9" viewBox="0 0 14 9"><path d="M1 1l6 6 6-6" stroke="#1d2129" stroke-width="1.8" fill="none"/></svg></div>
    <div class="abs sb-expand">Expand</div>
    <div class="abs sb-row" style="top:63px;border-bottom:none">Short-Term Memory<svg width="18" height="10" viewBox="0 0 18 10"><path d="M1 9l8-7 8 7" stroke="#555" stroke-width="1.6" fill="none"/></svg></div>
    <div class="abs sb-row word" style="top:106px;height:41px">Grab</div>
    <div class="abs sb-row" style="top:147px;border-top:1px solid var(--line)">Working Memory<svg width="18" height="10" viewBox="0 0 18 10"><path d="M1 1l8 7 8-7" stroke="#555" stroke-width="1.6" fill="none"/></svg></div>
    <div class="abs sb-row" style="top:191px">Long-Term Memory<svg width="18" height="10" viewBox="0 0 18 10"><path d="M1 1l8 7 8-7" stroke="#555" stroke-width="1.6" fill="none"/></svg></div>
  </aside>

  <div class="abs step" style="left:394px">
    <svg class="shape" width="250" height="57"><polygon points="0,0 235,0 247,28.5 235,57 0,57" fill="#2a5db0"/></svg>
    <div class="name" style="color:#fff">Review 1</div><div class="state" style="color:#dfe7f5">Completed</div>
    <div class="badge" style="left:188px;background:#fff"><svg width="18" height="18" viewBox="0 0 24 24"><path d="M12 2l3 7 7 .6-5.3 4.7 1.6 7.2L12 17.8 5.7 21.5l1.6-7.2L2 9.6 9 9z" fill="#f6a52a"/></svg></div>
  </div>
  <div class="abs step" style="left:652px">
    <svg class="shape" width="250" height="57"><polygon points="1,1 235,1 247,28.5 235,56 1,56 12,28.5" fill="#fff" stroke="#2a5db0" stroke-width="1.5"/></svg>
    <div class="name" style="left:34px">Review 2</div><div class="state" style="left:34px;color:var(--muted)">In Process</div>
    <div class="badge" style="left:192px;background:#2a5db0"><svg width="18" height="18" viewBox="0 0 24 24"><path d="M12 2l3 7 7 .6-5.3 4.7 1.6 7.2L12 17.8 5.7 21.5l1.6-7.2L2 9.6 9 9z" fill="#fff"/></svg></div>
  </div>
  <div class="abs step" style="left:909px">
    <svg class="shape" width="250" height="57"><polygon points="1,1 235,1 247,28.5 235,56 1,56 12,28.5" fill="#fafbfc" stroke="#eceef2"/></svg>
    <div class="name" style="left:29px;color:var(--faint)">Review 3</div><div class="state" style="left:29px;color:var(--faint)">Unvisited</div>
    <div class="badge" style="left:195px;background:#eef0f3"><svg width="18" height="18" viewBox="0 0 24 24"><path d="M12 2l3 7 7 .6-5.3 4.7 1.6 7.2L12 17.8 5.7 21.5l1.6-7.2L2 9.6 9 9z" fill="none" stroke="#9aa0a9" stroke-width="1.6"/></svg></div>
  </div>
  <div class="abs step" style="left:1167px">
    <svg class="shape" width="250" height="57"><polygon points="1,1 235,1 247,28.5 235,56 1,56 12,28.5" fill="#fafbfc" stroke="#eceef2"/></svg>
    <div class="name" style="left:29px;color:var(--faint)">Review 4</div><div class="state" style="left:29px;color:var(--faint)">Unvisited</div>
    <div class="badge" style="left:195px;background:#eef0f3"><svg width="18" height="18" viewBox="0 0 24 24"><path d="M12 2l3 7 7 .6-5.3 4.7 1.6 7.2L12 17.8 5.7 21.5l1.6-7.2L2 9.6 9 9z" fill="none" stroke="#9aa0a9" stroke-width="1.6"/></svg></div>
  </div>

  <h1 class="abs word-title">Grab <svg width="24" height="24" viewBox="0 0 24 24"><path d="M12 2l3 7 7 .6-5.3 4.7 1.6 7.2L12 17.8 5.7 21.5l1.6-7.2L2 9.6 9 9z" fill="#f2b705"/></svg></h1>
  <div class="abs start-btn"><svg width="20" height="20" viewBox="0 0 20 20"><circle cx="10" cy="10" r="10" fill="#fff"/><path d="M8 6l6 4-6 4z" fill="#262b33"/></svg>Start Vocabulary Review Exercise 3</div>
  <p class="abs intro">The word "grab" is most commonly used as a verb, meaning to take something quickly or suddenly. Imagine you're running late for school. You don't have time for breakfast, so you quickly grab an apple from the kitchen and rush out the door. As you reach the bus stop, your friend waves and says, "Hey! Let's grab a coffee after class." Later, when you sit down, your phone starts ringing. You grab it from your bag and answer.</p>

  <div class="abs card">
    <div class="abs card-icon"><svg width="22" height="20" viewBox="0 0 22 20"><path d="M2 18h18M3 18V9l4 3V6l4 3V3l4 3v12" stroke="#2a5db0" stroke-width="1.8" fill="none"/><path d="M15 5l3-3 2 2" stroke="#2a5db0" stroke-width="1.6" fill="none"/></svg></div>
    <div class="abs card-title">Learning Curve Graph</div>
    <div class="abs tabs"><span>1 day</span><span>1 week</span><span>1 month</span><span>1 year</span><span class="on">All Time</span></div>
    <div class="abs legend" style="top:121px;color:var(--orange)">Long-Term Memory</div>
    <div class="abs legend" style="top:172px;color:var(--purple)">Working Memory</div>
    <div class="abs legend" style="top:223px;color:var(--red)">Short-Term Memory</div>
    <div class="abs legend" style="top:274px;color:var(--sky)">Forgotten Memory</div>
    <svg class="abs" style="left:0;top:0" width="1031" height="388" viewBox="394 330 1031 388">
      <g stroke="#eceef2"><line x1="676" x2="1401" y1="459" y2="459"/><line x1="676" x2="1401" y1="510" y2="510"/><line x1="676" x2="1401" y1="561" y2="561"/><line x1="676" x2="1401" y1="612" y2="612"/><line x1="676" x2="1401" y1="661" y2="661"/></g>
      <g>
        <path d="M678 661V524a16 16 0 0 1 32 0V661z" fill="#5b4cf0"/>
        <path d="M740 661V475a16 16 0 0 1 32 0V661z" fill="#f6a52a"/>
        <path d="M802 661V627a16 16 0 0 1 32 0V661z" fill="#1e88e5"/>
        <path d="M864 661V577a16 16 0 0 1 32 0V661z" fill="#e8305a"/>
        <path d="M926 661V475a16 16 0 0 1 32 0V661z" fill="#f6a52a"/>
        <path d="M988 661V524a16 16 0 0 1 32 0V661z" fill="#5b4cf0"/>
        <path d="M1050 661V627a16 16 0 0 1 32 0V661z" fill="#1e88e5"/>
        <path d="M1112 661V577a16 16 0 0 1 32 0V661z" fill="#e8305a"/>
        <path d="M1174 661V475a16 16 0 0 1 32 0V661z" fill="#f6a52a"/>
        <path d="M1236 661V627a16 16 0 0 1 32 0V661z" fill="#1e88e5"/>
        <path d="M1298 661V524a16 16 0 0 1 32 0V661z" fill="#5b4cf0"/>
        <path d="M1360 661V577a16 16 0 0 1 32 0V661z" fill="#e8305a"/>
      </g>
      <g font-family="Inter, sans-serif" font-size="12" fill="#444" text-anchor="middle">
        <text x="694" y="685">Jan</text><text x="756" y="685">Feb</text><text x="818" y="685">Mar</text><text x="880" y="685">Apr</text><text x="942" y="685">May</text><text x="1004" y="685">Jun</text><text x="1066" y="685">Jul</text><text x="1128" y="685">Aug</text><text x="1190" y="685">Sep</text><text x="1252" y="685">Oct</text><text x="1314" y="685">Nov</text><text x="1376" y="685">Dec</text>
      </g>
    </svg>
  </div>

  <h2 class="abs analysis-title">QuillVane Learning Analysis</h2>
  <p class="abs analysis">Lorem ipsum dolor sit amet, consectetur adipiscing elit, sed do eiusmod tempor incididunt ut labore et dolore magna aliqua. Ut enim ad minim veniam, quis nostrud exercitation ullamco laboris nisi ut aliquip ex ea commodo consequat.</p>
  <div class="abs bottom-strip" style="left:78px;width:1362px"></div>

  <div class="abs dim"></div>

  <div class="abs modal">
    <div class="abs modal-head">All <svg width="14" height="9" viewBox="0 0 14 9"><path d="M1 1l6 6 6-6" stroke="#fff" stroke-width="1.8" fill="none"/></svg>
      <div class="abs modal-close"><svg width="10" height="10" viewBox="0 0 10 10"><path d="M1 1l8 8M9 1l-8 8" stroke="#e8305a" stroke-width="1.6"/></svg></div>
    </div>
    <div class="abs group-title" style="top:89px">Short-Term Memory</div>
    <div class="abs chips" style="top:123px"><span class="chip red">Grab</span></div>
    <div class="abs group-title" style="top:181px">Working Memory</div>
    <div class="abs chips" style="top:215px">
      <span class="chip purple">Cool Down</span><span class="chip purple">Crave</span><span class="chip purple">Go For</span><span class="chip purple">Go-To</span><span class="chip purple">In The Mood For</span>
      <span class="chip purple">Sip</span><span class="chip purple">Soothing</span><span class="chip purple">Stick With</span><span class="chip purple">Throw In/Throw On</span>
    </div>
    <div class="abs group-title" style="top:315px">Long-Term M</div>
    <div class="abs chips" style="top:349px"><span class="chip orange">Give It A Try</span></div>
  </div>
</section>

</body>
</html>
```